Media Services Start-up -- Corporate Website and Logo Design. Inspiration required!

We need a logo design and corporate website design, including coding, for our start-up business.
Vennatra’s value proposition is based on bringing together media content from a vast number of geographies globally, adding human and AI curation, translation and editing, and delivering the content using tailored customer interfaces. On the one hand, the business brings together media coverage from all over the world, and on the other it brings together content, human skills and technology to deliver a supreme customer experience.
Vennatra is a B2B media monitoring and analytics business with emphasis on global customers. Vennatra's service offering is centred around sourcing media content from different markets, processing, storing and delivering the content and insights derived from it using an online platform / mobile app.
The messaging we want to create through the logo is:
- Global scope
- Speed of delivery
- Cost-efficiency
- Multi-lingual
- Tailor-made
- Trustworthy
Target Market(s)
Business to business, PR / Communications, Media, Marketing
Logo Text
Vennatra
Coding
Coded - Design and coding required
Number of Pages Required
5+ page
Font styles to use
Other font styles liked:
- See Design Brief for details
Colors
Designer to choose colors to be used in the design.

```html
<!DOCTYPE html>
<html lang="en">
<head>
<meta charset="utf-8">
<title>Vennatra — Media Intelligence</title>
<link href="https://fonts.googleapis.com/css2?family=Roboto:wght@400;500;700;900&family=Poppins:wght@300;400;500&display=swap" rel="stylesheet">
<style>
:root{
  --board:#dfeaec;
  --ink:#1f2a36;
  --text:#3a3f47;
  --blue:#1243a0;
  --blue-deep:#0f3a8e;
  --night:#0f1320;
  --orange:#f6930d;
  --footer:#1e1e1e;
  --footer-bar:#1a1a1a;
  --white:#ffffff;
  --teal:#5fc9cf;
}
*{box-sizing:border-box;margin:0;padding:0}
html,body{width:1200px;height:3328px;overflow:hidden}
body{background:var(--board);font-family:'Poppins',sans-serif;color:var(--text);position:relative}
.page{position:absolute;left:149px;width:903px;overflow:hidden;box-shadow:0 2px 10px rgba(0,0,0,.12)}
.page--home{top:134px;height:545px;background:var(--night)}
.page--solutions{top:732px;height:2461px;background:var(--white)}
.abs{position:absolute}
.hero-photo{position:absolute;inset:0}
.page--home .hero-photo{background:radial-gradient(ellipse at 40% 30%,#3a3b44 0%,#1a1d28 45%,#0b0f1a 100%),#10131c}
.hero-glow{position:absolute;right:0;top:0;width:360px;height:100%;background:linear-gradient(90deg,rgba(20,40,55,0) 0%,rgba(40,90,110,.35) 100%)}
.logo{font-family:'Roboto',sans-serif;font-weight:700;color:var(--white);font-size:31px;letter-spacing:.3px}
.nav{display:flex;gap:0;font-family:'Roboto',sans-serif;font-weight:500;font-size:11.5px;color:var(--white);text-transform:uppercase}
.nav a{color:inherit;text-decoration:none;position:absolute;white-space:nowrap}
.hero-title{font-family:'Roboto',sans-serif;font-weight:900;color:var(--white);font-size:37px;line-height:44px;text-transform:uppercase}
.hero-text{font-family:'Roboto',sans-serif;font-size:13.5px;line-height:28.5px;color:var(--white);width:400px}
.btn-outline{border:1.5px solid var(--white);color:var(--white);font-family:'Roboto',sans-serif;font-weight:500;font-size:11px;display:flex;align-items:center;justify-content:center;border-radius:2px}
.lead-form{background:rgba(0,0,0,.85);border:2.5px solid #6fb7bd;border-top-left-radius:14px;border-bottom-right-radius:14px;padding:16px 17px}
.lead-form h3{font-family:'Roboto',sans-serif;font-weight:900;font-size:17px;line-height:24px;color:var(--white);text-transform:uppercase;margin-bottom:10px}
.lead-form label{display:block;font-family:'Roboto',sans-serif;font-size:9.5px;color:var(--white);margin-bottom:5px}
.lead-form .field{height:24px;background:var(--white);margin-bottom:16px;border-radius:1px}
.btn-solid{background:var(--orange);color:var(--white);font-family:'Roboto',sans-serif;font-weight:500;font-size:11px;width:112px;height:28px;display:flex;align-items:center;justify-content:center;margin-top:2px}
.home-footer{position:absolute;left:0;right:0;top:483px;border-top:1px solid rgba(255,255,255,.18)}
.copy{font-size:10px;color:var(--white)}
.socials{display:flex;gap:4px}
.socials span{width:19px;height:19px;border:1px solid rgba(255,255,255,.8);border-radius:50%;display:block;position:relative}
.socials span::after{content:"";position:absolute;left:6px;top:6px;width:5px;height:5px;border-radius:50%;background:rgba(255,255,255,.8)}
.page--solutions .hero-photo{height:270px;background:linear-gradient(90deg,#1a3e94 0%,#2049a6 55%,#2b5fb3 100%)}
.page-title{font-family:'Roboto',sans-serif;font-weight:700;font-size:36px;color:var(--white);width:100%;text-align:center}
.section-title{font-family:'Roboto',sans-serif;font-weight:500;font-size:25px;color:var(--ink)}
.rule{width:39px;height:3px;background:var(--blue)}
.intro{font-size:11px;line-height:20px;color:var(--text)}
.ticks{list-style:none;font-size:10.6px;line-height:17.5px;color:var(--text)}
.ticks li{position:relative;padding-left:20px}
.ticks li::before{content:"›";position:absolute;left:0;top:3px;width:10px;height:10px;border-radius:50%;background:var(--blue-deep);color:var(--white);font-size:10px;line-height:9px;text-align:center;font-weight:700}
.band{position:absolute;left:0;top:671px;width:903px;height:245px;background:var(--blue-deep);text-align:center;color:var(--white)}
.band h2{font-family:'Roboto',sans-serif;font-weight:500;font-size:24px;margin-top:56px}
.band .rule{background:var(--white);margin:14px auto 0}
.band p{font-family:'Roboto',sans-serif;font-size:13px;line-height:24.5px;margin:16px auto 0;width:520px}
.illus{border-radius:6px}
.site-footer{position:absolute;left:0;top:2120px;width:903px;height:261px;background:var(--footer)}
.footer-bar{position:absolute;left:0;top:2381px;width:903px;height:80px;background:var(--footer-bar);border-top:1px solid #333;text-align:center;color:var(--white);font-size:10px;line-height:78px}
.footer-logo{font-size:44px}
.footer-tag{font-family:'Poppins',sans-serif;font-size:13px;line-height:21px;color:var(--white);border-left:1.5px solid var(--white);padding-left:14px}
.contact{display:flex;align-items:center;gap:14px;color:var(--white)}
.contact .ico{width:32px;height:32px;border:1.5px solid var(--white);border-radius:50%;display:flex;align-items:center;justify-content:center}
.contact b{display:block;font-family:'Poppins',sans-serif;font-weight:500;font-size:14px;line-height:20px}
.contact span{font-size:13.5px;line-height:20px}
</style>
</head>
<body>

<section class="page page--home">
  <div class="hero-photo" role="img" aria-label="Photo of a woman touching a glowing screen at night with circuit lines"></div>
  <div class="hero-glow"></div>
  <div class="abs logo" style="left:107px;top:30px">Vennatra</div>
  <nav class="nav">
    <a style="left:355px;top:43px">Home</a>
    <a style="left:409px;top:43px">Solutions</a>
    <a style="left:496px;top:43px">How we do it</a>
    <a style="left:596px;top:43px">Our People</a>
    <a style="left:689px;top:43px">Our Technology</a>
  </nav>
  <h1 class="abs hero-title" style="left:107px;top:165px">Delivering Global<br>Media Intelligence</h1>
  <p class="abs hero-text" style="left:108px;top:263px">Vennatra is an international media intelligence service provider. We help communications teams build and operate truly global media monitoring and measurement programmes.</p>
  <div class="abs btn-outline" style="left:108px;top:365px;width:110px;height:32px">LEARN MORE</div>
  <form class="abs lead-form" style="left:560px;top:136px;width:235px;height:294px">
    <h3>Learn more about Vennatra</h3>
    <label>Name</label><div class="field"></div>
    <label>Email</label><div class="field"></div>
    <label>Phone</label><div class="field"></div>
    <div class="btn-solid">GET STARTED</div>
  </form>
  <div class="home-footer">
    <p class="abs copy" style="left:108px;top:24px">© 2019 Vennatra. All Rights Reserved.</p>
    <div class="abs socials" style="left:705px;top:22px"><span></span><span></span><span></span><span></span></div>
  </div>
</section>

<section class="page page--solutions">
  <div class="hero-photo" role="img" aria-label="Blue-tinted photo of a woman at a glowing screen with circuit lines"></div>
  <div class="abs logo" style="left:107px;top:29px">Vennatra</div>
  <nav class="nav">
    <a style="left:355px;top:44px">Home</a>
    <a style="left:409px;top:44px">Solutions</a>
    <a style="left:496px;top:44px">How we do it</a>
    <a style="left:596px;top:44px">Our People</a>
    <a style="left:689px;top:44px">Our Technology</a>
  </nav>
  <h1 class="abs page-title" style="left:0;top:168px">SOLUTIONS</h1>

  <h2 class="abs section-title" style="left:108px;top:338px">Content Sourcing</h2>
  <div class="abs rule" style="left:108px;top:384px"></div>
  <p class="abs intro" style="left:108px;top:406px;width:400px">We help you build a content strategy that meets your budget and coverage needs across earned media - Print, Online, TV and Radio.</p>
  <ul class="abs ticks" style="left:108px;top:460px;width:360px">
    <li style="margin-bottom:8px">Identify geographies and markets of interest</li>
    <li style="margin-bottom:8px">Build target media source lists to fulfil monitoring and measurement requirements</li>
    <li style="margin-bottom:8px">Using our transparent cost calculator, we help you with accurate budgeting and choices to ensure you meet your strategy and objectives</li>
    <li>Translate and localise keyword searches and editorial instructions into effecient source-/ country-/ provider-specific needs to minimise wasted content.</li>
  </ul>
  <div class="abs illus" style="left:549px;top:356px;width:222px;height:217px;background:linear-gradient(160deg,#d9e6fb 0%,#7fb4e6 55%,#3a4d8c 100%)" role="img" aria-label="Illustration of a desktop monitor and phone showing checklists"></div>

  <div class="band">
    <h2>Content Collection</h2>
    <div class="rule"></div>
    <p>We consolidate and manage the delivery of your global media content into a Cloud-based scalable media platform, taking the headache of content management away from your teams.</p>
  </div>

  <div class="abs illus" style="left:99px;top:996px;width:307px;height:306px;background:radial-gradient(circle at 70% 75%,#f9c34a 0%,#f2a93b 30%,#5fc8a1 60%,#e9f3ef 100%)" role="img" aria-label="Illustration of a document with a gear"></div>
  <h2 class="abs section-title" style="left:443px;top:982px">Content Augmentation</h2>
  <div class="abs rule" style="left:443px;top:1023px"></div>
  <ul class="abs ticks" style="left:443px;top:1048px;width:360px">
    <li style="margin-bottom:13px">We manage and normalise all of the source-level reference data - country, language, reach etc.</li>
    <li style="margin-bottom:13px">We add editorial validation to ensure only the content required reaches your delivery, removing inevitable noise from source providers</li>
    <li style="margin-bottom:13px">Tagging - AI and human based tagging to detect locations, people, topics, products, brands, services, etc.</li>
    <li style="margin-bottom:13px">Human and automated grouping of stories across geographies - clustering, "also-in" groupings etc.</li>
    <li style="margin-bottom:13px">Translation summarisation - AI Translation or human-created depending on budget, speed of delivery and need.</li>
    <li>Digest authoring - refining the essence of today's coverage into a concise board-ready output for your organisation</li>
  </ul>

  <h2 class="abs section-title" style="left:120px;top:1383px">Content Delivery</h2>
  <div class="abs rule" style="left:120px;top:1425px"></div>
  <p class="abs intro" style="left:120px;top:1441px;width:400px">Early morning delivery of a consolidated, ready-to-consume media coverage</p>
  <ul class="abs ticks" style="left:120px;top:1475px;width:350px">
    <li style="margin-bottom:13px">Customised email templates, delivering content in templates designed to meet your needs</li>
    <li style="margin-bottom:13px">Customised platform - modern portal tailored to meet your media management needs, removing the unwanted clutter and focusing on the job at hand</li>
    <li>Integration with Intranets, third-party communication tools e.g. chat apps, RSS readers, customised APIs</li>
  </ul>
  <div class="abs illus" style="left:585px;top:1406px;width:199px;height:200px;background:linear-gradient(160deg,#eef7fb 0%,#a9dcef 50%,#f5c443 100%)" role="img" aria-label="Illustration of a clipboard checklist and pencil"></div>

  <div class="abs illus" style="left:99px;top:1722px;width:301px;height:304px;background:linear-gradient(180deg,#eef5fb 0%,#cfe6f7 40%,#f5d66a 55%,#1f3f8f 80%,#3b3b3b 100%)" role="img" aria-label="Illustration of two people joining puzzle pieces"></div>
  <h2 class="abs section-title" style="left:445px;top:1704px">Media Insights &amp; Consultancy</h2>
  <div class="abs rule" style="left:445px;top:1745px"></div>
  <ul class="abs ticks" style="left:445px;top:1771px;width:350px">
    <li style="margin-bottom:13px">Levering the normalised content sets from your integrated monitoring service, we can analyse and tag your coverage based on complex qualitative measurement criteria, consistent across all languages and geographies, to combine with quantitative metrics.</li>
    <li style="margin-bottom:13px">Ability to create a single consistent measurement programme across all of your global operations.</li>
    <li style="margin-bottom:13px">Consultancy to HQ and local offices on how to utilise and align existing measurement and insight intiatives to provide continuity.</li>
    <li style="margin-bottom:13px">Customised online dashboards with near real time data insights, coupled with Board-ready offline reporting and export options.</li>
    <li>Integration with social media content, third-party data, point-of-sale, web analytics, and delivering on your Integrated Communications Framework</li>
  </ul>

  <footer class="site-footer">
    <div class="abs logo footer-logo" style="left:107px;top:85px">Vennatra</div>
    <div class="abs footer-tag" style="left:308px;top:95px">International media<br>intelligence service</div>
    <div class="abs socials" style="left:108px;top:148px"><span></span><span></span><span></span><span></span></div>
    <div class="abs contact" style="left:495px;top:41px">
      <div class="ico"><svg width="14" height="16" viewBox="0 0 14 16"><path d="M7 15s5-5.2 5-8.5A5 5 0 0 0 2 6.5C2 9.8 7 15 7 15z" fill="none" stroke="#fff" stroke-width="1.5"/><circle cx="7" cy="6.5" r="1.8" fill="#fff"/></svg></div>
      <div><b>Address:</b><span>Vennatra 14 Harbour Lane, Westbrook</span></div>
    </div>
    <div class="abs contact" style="left:495px;top:96px">
      <div class="ico"><svg width="14" height="14" viewBox="0 0 14 14"><path d="M3 1l2.5 3-1.5 1.5a8 8 0 0 0 4.5 4.5L10 8.5l3 2.5-1.5 2C6 13 1 8 1 2.5z" fill="none" stroke="#fff" stroke-width="1.4" stroke-linejoin="round"/></svg></div>
      <div><b>Phone:</b><span>(555) 0142-7730</span></div>
    </div>
    <div class="abs contact" style="left:495px;top:150px">
      <div class="ico"><svg width="15" height="12" viewBox="0 0 15 12"><rect x="1" y="1" width="13" height="10" rx="1" fill="none" stroke="#fff" stroke-width="1.3"/><path d="M1 2l6.5 5L14 2" fill="none" stroke="#fff" stroke-width="1.3"/></svg></div>
      <div><b>Email:</b><span>hello@vennatra.example</span></div>
    </div>
  </footer>
  <div class="footer-bar">© 2019 Vennatra. All Rights Reserved.</div>
</section>

</body>
</html>
```